New Innovative Counselling and psychotherapy Service needs Business Card design

Keep it simple and professional. On one side, just company name and logo (perhaps in all blue) and maybe a tag line.

On other side (all white) my name and Qualifications in centre

Industry/Entity Type

Health And Wellness

Contact Information for Business Card

Dara Whelby
Counsellor & Psychotherapist
BSc (Psychol.), BA, Dip. (Couns. & Psych.), PG.Cert (CBT), FGTrK, ONRE

I will also require Mobile no, Email and web site address of which I'll pass on to final designer.

Font styles to use
Sans Serif

Requirements
Must have
• My Logo Only and please use the colours in logo that is in it.
Should not have
• Any other images

```html
<!DOCTYPE html>
<html lang="en">
<head>
<meta charset="utf-8">
<title>Lantern Way – Business Card</title>
<link href="https://fonts.googleapis.com/css2?family=Montserrat:wght@400&family=Roboto:wght@400;700&display=swap" rel="stylesheet">
<style>
  :root {
    --backdrop: #3b3b3d;
    --card-dark: #1f1f21;
    --card-front: #232325;
    --front-mark: #3c3c3f;
    --brand-blue: #3daeea;
    --brand-green: #8bd14a;
    --text-light: #f2f2f2;
    --text-muted: #d0d0d0;
    --text-dark: #141414;
  }
  * { margin: 0; padding: 0; box-sizing: border-box; }
  html, body { width: 799px; height: 1200px; overflow: hidden; }
  body {
    background: var(--backdrop);
    font-family: "Roboto", Arial, sans-serif;
    position: relative;
  }
  .card {
    position: absolute;
    left: 80px;
    width: 640px;
    height: 380px;
    border-radius: 26px;
    overflow: hidden;
    box-shadow: 0 14px 30px rgba(0,0,0,0.45);
  }
  .card--front { top: 110px; background: var(--card-front); }
  .card--back { top: 700px; background: var(--card-dark); }

  .front-brand {
    position: absolute;
    inset: 0;
    display: flex;
    align-items: center;
    justify-content: center;
    gap: 18px;
  }
  .front-brand__dot {
    width: 56px; height: 56px; border-radius: 50%;
    background: var(--front-mark);
  }
  .front-brand__name {
    font-family: "Montserrat", Arial, sans-serif;
    font-weight: 400;
    font-size: 44px;
    color: var(--front-mark);
  }

  .back-wave { position: absolute; inset: 0; width: 100%; height: 100%; }
  .back-brand {
    position: absolute;
    top: 30px; left: 32px;
    display: flex; align-items: center; gap: 22px;
  }
  .back-brand__dot {
    width: 58px; height: 58px; border-radius: 50%;
    background: var(--brand-blue);
  }
  .back-brand__name {
    font-family: "Montserrat", Arial, sans-serif;
    font-weight: 400;
    font-size: 44px;
    color: var(--text-light);
    letter-spacing: 0.5px;
  }
  .person {
    position: absolute;
    top: 112px; left: 32px;
  }
  .person__name {
    font-weight: 700;
    font-size: 24px;
    color: var(--brand-blue);
    margin-bottom: 4px;
  }
  .person__line {
    font-size: 14px;
    line-height: 17px;
    color: var(--text-muted);
  }
  .contact {
    position: absolute;
    right: 32px; bottom: 26px;
    list-style: none;
    text-align: right;
  }
  .contact__item {
    display: flex; align-items: center; justify-content: flex-end; gap: 10px;
    font-size: 17px; line-height: 25px;
    color: var(--text-dark);
  }
  .contact__icon { width: 16px; height: 16px; fill: var(--text-dark); }
</style>
</head>
<body>

<section class="card card--front" aria-label="Card front">
  <div class="front-brand">
    <span class="front-brand__dot"></span>
    <span class="front-brand__name">Lantern Way</span>
  </div>
</section>

<section class="card card--back" aria-label="Card back">
  <svg class="back-wave" viewBox="0 0 640 380" preserveAspectRatio="none">
    <path d="M0 230 C120 215 200 270 330 285 C460 300 560 265 640 235 L640 380 L0 380 Z" fill="var(--brand-blue)"/>
    <path d="M0 218 C120 200 200 255 330 268 C460 282 560 250 640 222" fill="none" stroke="var(--card-dark)" stroke-width="10"/>
    <path d="M60 206 C150 200 220 250 330 262 C460 276 560 246 640 214" fill="none" stroke="var(--brand-green)" stroke-width="7"/>
  </svg>

  <div class="back-brand">
    <span class="back-brand__dot"></span>
    <span class="back-brand__name">Lantern Way</span>
  </div>

  <div class="person">
    <p class="person__name">Dara Whelby</p>
    <p class="person__line">Counsellor &amp; Psychotherapist</p>
    <p class="person__line">BSc (Psychol.), BA, Dip. (Couns. &amp; Psych.),</p>
    <p class="person__line">PG.Cert (CBT), FGTrK, ONRE</p>
  </div>

  <ul class="contact">
    <li class="contact__item">0987 654 3210
      <svg class="contact__icon" viewBox="0 0 16 16"><path d="M3 1h3l1 4-2 1c1 2 3 4 5 5l1-2 4 1v3c0 1-1 2-2 2C7 15 1 9 1 3c0-1 1-2 2-2z"/></svg>
    </li>
    <li class="contact__item">www.LanternWay.com
      <svg class="contact__icon" viewBox="0 0 16 16"><path d="M1 3h14v10H1z M2 4l6 5 6-5" fill="none" stroke="var(--text-dark)" stroke-width="1.6"/></svg>
    </li>
    <li class="contact__item">dara.w@LanternWay.com
      <svg class="contact__icon" viewBox="0 0 16 16"><circle cx="8" cy="8" r="6.5" fill="none" stroke="var(--text-dark)" stroke-width="1.5"/><ellipse cx="8" cy="8" rx="2.8" ry="6.5" fill="none" stroke="var(--text-dark)" stroke-width="1.2"/><path d="M1.5 8h13" stroke="var(--text-dark)" stroke-width="1.2"/></svg>
    </li>
  </ul>
</section>

</body>
</html>
```